Design a Travel and Tourism website

We would like a freelancer to design a website that is essentially easy to use and navigate database providing local information for Travelers about destination countries.

We proposed website would discuss different rates, fees, visa requirement, resort locations, cheap flights, etc. This website should be elegant and modern. Our business name is rovanix.
Some reference websites are zemplorift.ca, brindlefoxhaven.com,
There should be a forum in the website where travell\ers discuss about their first hand tranvel experience to such destinations.

Tourism

```html
<!DOCTYPE html>
<html lang="en">
<head>
<meta charset="utf-8">
<title>Rovanix — Travel &amp; Tourism</title>
<link href="https://fonts.googleapis.com/css2?family=Playball&family=Open+Sans:wght@400;600;700&display=swap" rel="stylesheet">
<style>
:root{
  --navy:#0b2657;
  --navy-dark:#081d44;
  --blue:#1d64b3;
  --blue-light:#3b86d1;
  --gold:#c8a548;
  --gold-dark:#a98a33;
  --text:#3a3f4a;
  --muted:#8a909a;
  --line:#e2e5ea;
  --bg:#ffffff;
  --soft:#f5f6f8;
}
*{box-sizing:border-box;margin:0;padding:0}
html,body{width:1200px;height:3276px;overflow:hidden}
body{font-family:"Open Sans",Arial,sans-serif;color:var(--text);background:var(--bg);position:relative}
.script{font-family:"Playball",cursive;font-weight:400}
a{color:inherit;text-decoration:none}

/* header */
.site-header{position:absolute;top:0;left:0;width:1200px;height:60px;background:rgba(255,255,255,.96);z-index:5}
.utility{position:absolute;top:4px;right:40px;font-size:10px;color:var(--muted);letter-spacing:.5px}
.utility span{margin-left:12px}
.nav{position:absolute;top:22px;font-size:12px;font-weight:700;color:var(--navy);display:flex;gap:6px}
.nav a{padding:8px 14px;border-radius:3px}
.nav.left{left:140px}
.nav.right{right:140px}
.nav a.active{background:var(--gold);color:#fff}
.brand{position:absolute;left:520px;top:0;width:160px;height:86px;background:#fff;border-radius:0 0 14px 14px;display:flex;flex-direction:column;align-items:center;justify-content:center;box-shadow:0 3px 8px rgba(0,0,0,.15)}
.brand-name{font-family:"Open Sans",sans-serif;font-weight:700;font-size:26px;color:var(--navy)}
.brand-dot{width:10px;height:10px;border-radius:50%;background:var(--gold);margin-bottom:4px}
.brand-tag{font-size:8px;color:var(--muted);letter-spacing:2px}

/* hero */
.hero{position:absolute;top:0;left:0;width:1200px;height:470px;background:linear-gradient(180deg,#7fa6c9 0%,#4a7fa0 35%,#3f6f4f 65%,#1d4d7a 100%)}
.hero-title{position:absolute;left:200px;top:120px;font-size:58px;line-height:1.05;color:#fff;text-shadow:0 2px 6px rgba(0,0,0,.35)}
.promo{position:absolute;left:830px;top:140px;width:150px;height:150px;border-radius:50%;background:linear-gradient(160deg,#3f83c8,#123c7a);border:4px solid #fff}

/* search */
.search{position:absolute;top:470px;left:0;width:1200px;height:130px;background:var(--navy);padding:16px 140px}
.tabs{display:flex;gap:4px;font-size:10px;font-weight:700;color:#c9d3e6}
.tabs span{padding:6px 12px;border:1px solid rgba(255,255,255,.25);border-radius:2px}
.tabs span.active{background:var(--gold);border-color:var(--gold);color:#fff}
.fields{display:flex;gap:10px;margin-top:10px}
.field{flex:1}
.field label{display:block;font-size:9px;color:#aebbd4;font-weight:600;margin-bottom:3px;letter-spacing:.5px}
.field div{height:26px;background:#fff;border-radius:2px;font-size:10px;color:var(--muted);padding:6px 8px}
.field.small{flex:0 0 70px}
.search-actions{display:flex;align-items:center;gap:14px;margin-top:10px;font-size:10px;color:#fff;font-weight:600}
.check{width:12px;height:12px;border:1px solid #fff;display:inline-block;vertical-align:middle;margin-right:6px}
.btn-search{background:var(--blue-light);color:#fff;padding:7px 22px;border-radius:2px;font-weight:700}

/* section headings */
.section-title{text-align:center;font-size:40px;color:var(--navy)}
.section-title.gold{color:var(--gold)}
.subtabs{text-align:center;font-size:9px;font-weight:700;color:var(--muted);letter-spacing:.6px;margin-top:6px}
.subtabs span{padding:0 10px;border-left:1px solid var(--line)}
.subtabs span:first-child{border:0;color:var(--blue)}
.btn-view{display:block;width:84px;margin:0 auto;text-align:center;font-size:10px;font-weight:700;color:var(--blue);border:1px solid var(--blue);border-radius:2px;padding:6px 0}

/* holidays */
.holidays{position:absolute;top:640px;left:0;width:1200px;height:600px}
.dest-grid{display:grid;grid-template-columns:repeat(3,300px);grid-auto-rows:200px;gap:6px;justify-content:center;margin-top:26px}
.dest{position:relative;display:flex;align-items:center;justify-content:center;color:#fff;font-size:28px;text-shadow:0 2px 5px rgba(0,0,0,.5)}
.dest-cruise{background:linear-gradient(160deg,#5b9bd0,#1d5d9a)}
.dest-ny{background:linear-gradient(160deg,#e7b46a,#8a6a4a)}
.dest-island{background:linear-gradient(160deg,#3fa8c8,#176a8c)}
.dest-paris{background:linear-gradient(160deg,#f0a25a,#b35a38)}
.dest-london{background:linear-gradient(160deg,#4a5a80,#1d2a4a)}
.dest-hawaii{background:linear-gradient(160deg,#d78a5a,#5a3a3a)}
.holidays .btn-view{margin-top:22px}

/* hotels */
.hotels{position:absolute;top:1270px;left:0;width:1200px;height:490px;background:linear-gradient(180deg,#2a78c4,#1b5ea8)}
.hotels .section-title{color:#fff;padding-top:22px}
.hotels .subtabs{color:#cfe0f3}
.hotels .subtabs span{border-color:rgba(255,255,255,.35)}
.hotels .subtabs span:first-child{color:#fff}
.hotel-row{display:flex;gap:22px;justify-content:center;margin-top:22px}
.hotel{width:300px}
.hotel-img{height:160px}
.hotel-1{background:linear-gradient(160deg,#8fb3d9,#3d5f84)}
.hotel-2{background:linear-gradient(160deg,#d8c6a6,#7e6e56)}
.hotel-3{background:linear-gradient(160deg,#a8c4e0,#3a5677)}
.hotel-info{color:#fff;padding-top:8px}
.hotel-info h3{font-size:13px;font-weight:700}
.hotel-info p{font-size:9px;color:#cfe0f3;margin:2px 0 4px}
.stars{color:var(--gold);font-size:12px;letter-spacing:1px}
.arrow{position:absolute;top:1490px;width:20px;height:30px;z-index:2}
.hotels .btn-view{margin-top:20px;color:#fff;border-color:#fff}

/* forum */
.forum{position:absolute;top:1790px;left:0;width:1200px;height:520px}
.forum-table{width:920px;margin:22px auto 0;border-collapse:collapse;font-size:10px}
.forum-table th{background:var(--gold);color:#fff;text-align:left;padding:8px 12px;font-weight:700;letter-spacing:.5px}
.forum-table td{padding:10px 12px;border-bottom:1px solid var(--line);vertical-align:top}
.forum-table tr:nth-child(even) td{background:var(--soft)}
.topic{color:var(--gold-dark);font-weight:600;font-size:11px}
.by{color:var(--muted);font-size:9px;margin-top:3px}
.meta{color:var(--muted);font-size:9px}
.forum .btn-view{margin-top:22px}

/* newsletter */
.newsletter{position:absolute;top:2340px;left:0;width:1200px;height:160px;background:linear-gradient(90deg,var(--navy-dark),var(--navy),var(--navy-dark));text-align:center;color:#fff;padding-top:24px}
.newsletter h2{font-size:32px}
.newsletter p{font-size:9px;letter-spacing:1px;color:#aebbd4}
.subscribe{display:flex;justify-content:center;margin-top:14px}
.subscribe div{width:360px;height:32px;background:#fff;border-radius:2px 0 0 2px;font-size:10px;color:var(--muted);text-align:left;padding:9px 12px}
.subscribe span{background:var(--gold);font-size:10px;font-weight:700;padding:9px 20px;border-radius:0 2px 2px 0}

/* popular links */
.popular{position:absolute;top:2530px;left:0;width:1200px;height:340px}
.popular .section-title{color:var(--gold)}
.link-grid{display:grid;grid-template-columns:repeat(3,270px);gap:14px 40px;justify-content:center;margin-top:26px}
.pill{height:36px;border:1px solid var(--line);border-radius:18px;display:flex;align-items:center;padding-left:14px;font-size:11px;color:var(--text)}
.pill svg{margin-right:10px}

/* footer */
.site-footer{position:absolute;top:2880px;left:0;width:1200px;height:396px;background:linear-gradient(180deg,#fff 0%,#eef3fa 45%,#9fbde0 100%);text-align:center}
.site-footer .brand-name{font-size:28px;display:block;margin-top:30px}
.socials{display:flex;justify-content:center;gap:8px;margin-top:12px}
.socials span{width:24px;height:24px;border-radius:50%;background:var(--navy)}
.footer-links{font-size:10px;font-weight:700;color:var(--navy);margin-top:16px}
.footer-links span{margin:0 8px}
.copyright{font-size:9px;color:var(--muted);margin-top:6px}
.skyline{position:absolute;left:0;bottom:0;width:1200px;height:170px;background:linear-gradient(180deg,#3a6fae,#0b2657)}
</style>
</head>
<body>

<header class="site-header">
  <div class="utility"><span>MY ACCOUNT</span><span>LOGIN</span><span>REGISTER</span></div>
  <nav class="nav left"><a class="active">HOME</a><a>HOLIDAYS</a><a>FLIGHTS</a><a>HOTELS</a></nav>
  <div class="brand"><span class="brand-dot"></span><span class="brand-name">Rovanix</span><span class="brand-tag">TRAVEL GUIDE</span></div>
  <nav class="nav right"><a>CARS</a><a>DEALS</a><a>INSURANCE</a><a>FORUM</a></nav>
</header>

<section class="hero" role="img" aria-label="Coastal mountain landscape with sea and green cliffs">
  <h1 class="hero-title script">Start Your Dream<br>Holidays Right Here</h1>
  <div class="promo" role="img" aria-label="Round promotional badge for beach holidays"></div>
</section>

<section class="search">
  <div class="tabs"><span class="active">FLIGHT+HOTEL</span><span>HOLIDAYS</span><span>FLIGHTS</span><span>HOTELS</span><span>CARS</span><span>INSURANCE</span><span>EXTRAS</span></div>
  <div class="fields">
    <div class="field"><label>LEAVING FROM</label><div>City or airport</div></div>
    <div class="field"><label>GOING TO</label><div>City or airport</div></div>
    <div class="field"><label>DEPARTURE</label><div>dd/mm/yyyy</div></div>
    <div class="field"><label>RETURN</label><div>dd/mm/yyyy</div></div>
    <div class="field small"><label>NIGHTS</label><div>7</div></div>
    <div class="field small"><label>ADULTS</label><div>2</div></div>
    <div class="field small"><label>CHILDREN</label><div>0</div></div>
  </div>
  <div class="search-actions"><span><i class="check"></i>ADD A CAR</span><span class="btn-search">SEARCH</span></div>
</section>

<section class="holidays">
  <h2 class="section-title script">Holidays &amp; Destinations</h2>
  <div class="subtabs"><span>POPULAR HOLIDAYS</span><span>PERSONAL DESTINATIONS</span><span>MOST VISITED DESTINATIONS</span></div>
  <div class="dest-grid">
    <div class="dest dest-cruise script" role="img" aria-label="Cruise ship at sea">Cruise Holidays</div>
    <div class="dest dest-ny script" role="img" aria-label="New York skyline">New York Holidays</div>
    <div class="dest dest-island script" role="img" aria-label="Tropical island from above">Island Holidays</div>
    <div class="dest dest-paris script" role="img" aria-label="Paris at sunset">Paris Holidays</div>
    <div class="dest dest-london script" role="img" aria-label="London riverside at dusk">London Holidays</div>
    <div class="dest dest-hawaii script" role="img" aria-label="Hawaiian beach scene">Hawaii Holidays</div>
  </div>
  <a class="btn-view">VIEW ALL</a>
</section>

<section class="hotels">
  <h2 class="section-title script">Hotels</h2>
  <div class="subtabs"><span>LUXURY HOTELS</span><span>BUDGET HOTELS</span><span>RESORT HOTELS</span></div>
  <div class="hotel-row">
    <article class="hotel"><div class="hotel-img hotel-1" role="img" aria-label="Modern glass hotel tower in London"></div>
      <div class="hotel-info"><h3>London, UK</h3><p>Riverside rooms near the city centre</p><div class="stars">★★★★★</div></div></article>
    <article class="hotel"><div class="hotel-img hotel-2" role="img" aria-label="Classic stone hotel facade in Paris"></div>
      <div class="hotel-info"><h3>Paris, France</h3><p>Elegant suites close to the old town</p><div class="stars">★★★★★</div></div></article>
    <article class="hotel"><div class="hotel-img hotel-3" role="img" aria-label="Contemporary hotel building in Berlin"></div>
      <div class="hotel-info"><h3>Berlin, Germany</h3><p>Business hotel beside the main station</p><div class="stars">★★★★★</div></div></article>
  </div>
  <a class="btn-view">VIEW ALL</a>
</section>
<svg class="arrow" style="left:40px" viewBox="0 0 20 30"><path d="M15 3 L5 15 L15 27" fill="none" stroke="#fff" stroke-width="3"/></svg>
<svg class="arrow" style="right:40px" viewBox="0 0 20 30"><path d="M5 3 L15 15 L5 27" fill="none" stroke="#fff" stroke-width="3"/></svg>

<section class="forum">
  <h2 class="section-title gold script">Latest Travel Forum</h2>
  <div class="subtabs"><span>SHARE YOUR FIRST HAND EXPERIENCE</span></div>
  <table class="forum-table">
    <thead><tr><th style="width:55%">TITLE</th><th>POSTED ON</th><th style="text-align:right">VIEWS / REPLIES</th></tr></thead>
    <tbody>
      <tr><td><div class="topic">Why Hawaii's a hub for entertainment?</div><div class="by">By: Thomas Blake</div></td><td class="meta">12 Jan 2017, 09:40 AM</td><td class="meta" style="text-align:right">Views: 1240<br>Replies: 32</td></tr>
      <tr><td><div class="topic">Who the hottest place in January?</div><div class="by">By: Mira Lowden</div></td><td class="meta">12 Jan 2017, 10:15 AM</td><td class="meta" style="text-align:right">Views: 860<br>Replies: 18</td></tr>
      <tr><td><div class="topic">Most visit destinations in the world which make you feel better...</div><div class="by">By: Thomas Blake</div></td><td class="meta">11 Jan 2017, 04:20 PM</td><td class="meta" style="text-align:right">Views: 2105<br>Replies: 47</td></tr>
      <tr><td><div class="topic">Why Hawaii's a hub for entertainment?</div><div class="by">By: Thomas Blake</div></td><td class="meta">11 Jan 2017, 02:05 PM</td><td class="meta" style="text-align:right">Views: 540<br>Replies: 11</td></tr>
      <tr><td><div class="topic">Who the hottest place in January?</div><div class="by">By: Mira Lowden</div></td><td class="meta">10 Jan 2017, 08:30 AM</td><td class="meta" style="text-align:right">Views: 990<br>Replies: 25</td></tr>
    </tbody>
  </table>
  <a class="btn-view">VIEW ALL</a>
</section>

<section class="newsletter">
  <h2 class="script">Sign up to our Newsletter</h2>
  <p>GET INFORMATION FOR SPECIAL OFFERS</p>
  <div class="subscribe"><div>Enter your email address</div><span>SUBMIT</span></div>
</section>

<section class="popular">
  <h2 class="section-title script">Popular Links You may Interested</h2>
  <div class="link-grid">
    <div class="pill"><svg width="12" height="10" viewBox="0 0 12 10"><path d="M1 5 L4.5 8.5 L11 1.5" fill="none" stroke="#1d64b3" stroke-width="2"/></svg>New York Holidays</div>
    <div class="pill"><svg width="12" height="10" viewBox="0 0 12 10"><path d="M1 5 L4.5 8.5 L11 1.5" fill="none" stroke="#1d64b3" stroke-width="2"/></svg>Amsterdam Hotels</div>
    <div class="pill"><svg width="12" height="10" viewBox="0 0 12 10"><path d="M1 5 L4.5 8.5 L11 1.5" fill="none" stroke="#1d64b3" stroke-width="2"/></svg>Dubai Holidays</div>
    <div class="pill"><svg width="12" height="10" viewBox="0 0 12 10"><path d="M1 5 L4.5 8.5 L11 1.5" fill="none" stroke="#1d64b3" stroke-width="2"/></svg>UK Car Hire</div>
    <div class="pill"><svg width="12" height="10" viewBox="0 0 12 10"><path d="M1 5 L4.5 8.5 L11 1.5" fill="none" stroke="#1d64b3" stroke-width="2"/></svg>Bangkok Flights</div>
    <div class="pill"><svg width="12" height="10" viewBox="0 0 12 10"><path d="M1 5 L4.5 8.5 L11 1.5" fill="none" stroke="#1d64b3" stroke-width="2"/></svg>Bangkok Flights</div>
    <div class="pill"><svg width="12" height="10" viewBox="0 0 12 10"><path d="M1 5 L4.5 8.5 L11 1.5" fill="none" stroke="#1d64b3" stroke-width="2"/></svg>Sydney Flights</div>
    <div class="pill"><svg width="12" height="10" viewBox="0 0 12 10"><path d="M1 5 L4.5 8.5 L11 1.5" fill="none" stroke="#1d64b3" stroke-width="2"/></svg>Hawaii Hotels</div>
    <div class="pill"><svg width="12" height="10" viewBox="0 0 12 10"><path d="M1 5 L4.5 8.5 L11 1.5" fill="none" stroke="#1d64b3" stroke-width="2"/></svg>Paris Car Hire</div>
    <div class="pill"><svg width="12" height="10" viewBox="0 0 12 10"><path d="M1 5 L4.5 8.5 L11 1.5" fill="none" stroke="#1d64b3" stroke-width="2"/></svg>New York Holidays</div>
    <div class="pill"><svg width="12" height="10" viewBox="0 0 12 10"><path d="M1 5 L4.5 8.5 L11 1.5" fill="none" stroke="#1d64b3" stroke-width="2"/></svg>Amsterdam Hotels</div>
    <div class="pill"><svg width="12" height="10" viewBox="0 0 12 10"><path d="M1 5 L4.5 8.5 L11 1.5" fill="none" stroke="#1d64b3" stroke-width="2"/></svg>Dubai Holidays</div>
    <div class="pill"><svg width="12" height="10" viewBox="0 0 12 10"><path d="M1 5 L4.5 8.5 L11 1.5" fill="none" stroke="#1d64b3" stroke-width="2"/></svg>UK Car Hire</div>
    <div class="pill"><svg width="12" height="10" viewBox="0 0 12 10"><path d="M1 5 L4.5 8.5 L11 1.5" fill="none" stroke="#1d64b3" stroke-width="2"/></svg>Orlando Flights</div>
    <div class="pill"><svg width="12" height="10" viewBox="0 0 12 10"><path d="M1 5 L4.5 8.5 L11 1.5" fill="none" stroke="#1d64b3" stroke-width="2"/></svg>Bangkok Flights</div>
  </div>
</section>

<footer class="site-footer">
  <span class="brand-name">Rovanix</span>
  <div class="socials"><span></span><span></span><span></span></div>
  <div class="footer-links"><span>HOME</span><span>ABOUT US</span><span>CUSTOMER SUPPORT</span><span>PRIVACY</span><span>TERMS OF USE</span></div>
  <div class="copyright">© 2017 Rovanix. All rights reserved.</div>
  <div class="skyline" role="img" aria-label="City skyline silhouette at dusk"></div>
</footer>

</body>
</html>
```